RW Framewell Inc Business cards

We need business cards using our existing logo but slightly modified. Right now the logo says RW Loadbearing Masonry. We want to keep the RW part of the design, but replace the Structural Concrete portion with "FRAMEWELL". Please see the attached file.
Ideally this would be a blank template so we can add Different Names, titles, and phone numbers later.
On the one side we want only the logo and on the other side the detail. I'm attaching an example for you to see.
Please reach out with any other questions. Our address and other details will be given out once we find a design we like.

Target Market(s)

Construction Industry

```html
<!DOCTYPE html>
<html lang="en">
<head>
<meta charset="utf-8">
<title>RW Framewell Inc – Business Cards</title>
<link href="https://fonts.googleapis.com/css2?family=Montserrat:wght@600&family=Roboto:wght@400;500;700&display=swap" rel="stylesheet">
<style>
  :root {
    --brand-blue: #1562b2;
    --card-white: #ffffff;
    --backdrop: #8a8a8a;
    --ink-light: #ffffff;
    --brand-grey: #6b6d70;
  }
  * { margin: 0; padding: 0; box-sizing: border-box; }
  html, body {
    width: 1200px; height: 1106px; overflow: hidden;
    background: var(--backdrop);
  }
  .sheet {
    position: relative; width: 1200px; height: 1106px;
  }
  .card {
    position: absolute; left: 180px; width: 840px; height: 480px;
    box-shadow: 0 12px 30px rgba(0,0,0,.35);
    overflow: hidden;
  }
  .card--front { top: 50px; background: var(--brand-blue); }
  .card--back { top: 576px; background: var(--card-white); display: flex; }

  .wordmark {
    font-family: "Montserrat", sans-serif;
    font-weight: 600;
    letter-spacing: 6px;
    text-transform: uppercase;
    white-space: nowrap;
  }
  .card--front .wordmark {
    position: absolute; inset: 0;
    display: flex; align-items: center; justify-content: center;
    color: var(--ink-light);
    font-size: 54px;
  }
  .back-brand {
    width: 46%;
    display: flex; align-items: center; justify-content: center;
  }
  .back-brand .wordmark {
    color: var(--brand-blue);
    font-size: 32px;
    letter-spacing: 4px;
  }
  .back-details {
    width: 54%;
    background: var(--brand-blue);
    color: var(--ink-light);
    font-family: "Roboto", sans-serif;
    padding: 112px 0 0 70px;
  }
  .person-name { font-weight: 700; font-size: 30px; line-height: 1.1; }
  .person-title { font-weight: 500; font-size: 22px; margin-bottom: 22px; }
  .address { font-size: 22px; line-height: 1.25; margin-bottom: 6px; }
  .contact-list { list-style: none; font-size: 22px; line-height: 1.3; }
  .contact-list li { display: flex; align-items: center; gap: 12px; }
  .contact-list svg { width: 20px; height: 20px; flex: none; fill: none; stroke: var(--ink-light); stroke-width: 1.8; }
</style>
</head>
<body>
<main class="sheet">
  <section class="card card--front" aria-label="Business card front">
    <div class="wordmark">RW Framewell</div>
  </section>

  <section class="card card--back" aria-label="Business card back">
    <div class="back-brand">
      <div class="wordmark">RW Framewell</div>
    </div>
    <div class="back-details">
      <p class="person-name">Lena Hartwig</p>
      <p class="person-title">Director</p>
      <p class="address">Ahornweg 14,<br>80337 München</p>
      <ul class="contact-list">
        <li>
          <svg viewBox="0 0 20 20" aria-hidden="true"><rect x="5" y="1.5" width="10" height="17" rx="2"/><line x1="9" y1="15.5" x2="11" y2="15.5"/></svg>
          +49 170 555 010 20
        </li>
        <li>
          <svg viewBox="0 0 20 20" aria-hidden="true"><path d="M2 7 q8-5 16 0 v2 h-4 v-2 h-8 v2 h-4 z"/><rect x="4" y="10" width="12" height="7" rx="1"/></svg>
          +49 89 555 018 30
        </li>
        <li>
          <svg viewBox="0 0 20 20" aria-hidden="true"><rect x="2" y="4.5" width="16" height="11"/><path d="M2 4.5 l8 6.5 l8-6.5"/></svg>
          info@framewell.example
        </li>
        <li>
          <svg viewBox="0 0 20 20" aria-hidden="true"><circle cx="10" cy="10" r="8"/><ellipse cx="10" cy="10" rx="3.5" ry="8"/><line x1="2" y1="10" x2="18" y2="10"/></svg>
          www.framewell.example
        </li>
      </ul>
    </div>
  </section>
</main>
</body>
</html>
```